holloway paving service

Needs to have phone number 0418259730 and email markholloway@brightmail.com.au.
ABN 62318470915
name mark holloway

For all your concreting solutions
Excavation
Exposed & colour concrete
House & shed slabs
Driveways
Landing & steps

Contact Information for Business Card

ph 0418259730
email markholloway@brightmail.com.au.
ABN 62318470915
name mark holloway

```html
<!DOCTYPE html>
<html lang="en">
<head>
<meta charset="utf-8">
<title>Holloway Paving Service – Business Card</title>
<link href="https://fonts.googleapis.com/css2?family=Lato:wght@400;700&family=Oswald:wght@500&display=swap" rel="stylesheet">
<style>
  :root {
    --backdrop: #2b2b2b;
    --card: #1c1c1c;
    --card-edge: #161616;
    --pattern-light: #3a3a3a;
    --pattern-dark: #141414;
    --accent: #f26a21;
    --text: #f2f2f2;
  }
  * { margin: 0; padding: 0; box-sizing: border-box; }
  html, body { width: 1200px; height: 900px; overflow: hidden; }
  body {
    background: var(--backdrop);
    font-family: "Lato", Arial, sans-serif;
    color: var(--text);
    position: relative;
  }
  .card {
    position: absolute;
    left: 260px;
    width: 680px;
    height: 388px;
    background: var(--card);
    border: 1px solid var(--card-edge);
    overflow: hidden;
  }
  .card--back { top: 42px; }
  .card--front { top: 470px; }

  /* Back side */
  .back-pattern {
    position: absolute; inset: 0;
    background: linear-gradient(135deg, var(--pattern-dark) 0%, #222 45%, var(--pattern-light) 100%);
  }
  .back-brand {
    position: absolute;
    left: 440px; top: 218px;
    display: flex; align-items: center; gap: 8px;
    font-weight: 700; font-size: 13px; letter-spacing: 0.5px;
    color: var(--accent); text-transform: uppercase;
  }
  .brand-square {
    width: 26px; height: 26px; background: var(--accent); flex: none;
  }

  /* Front side */
  .front-brand {
    position: absolute; left: 0; right: 0; top: 52px;
    display: flex; justify-content: center; align-items: center; gap: 14px;
  }
  .front-brand .brand-square { width: 48px; height: 48px; }
  .brand-rule { width: 2px; height: 62px; background: var(--accent); }
  .brand-text { display: flex; flex-direction: column; gap: 4px; }
  .brand-name {
    font-weight: 700; font-size: 17px; letter-spacing: 0.6px;
    color: var(--accent); text-transform: uppercase;
  }
  .brand-phone {
    font-size: 12px; letter-spacing: 2px; color: var(--accent); text-align: center;
  }

  .person {
    position: absolute; right: 376px; top: 160px; text-align: right;
  }
  .person-name {
    font-family: "Oswald", "Arial Narrow", sans-serif;
    font-weight: 500; font-size: 36px; line-height: 1;
    color: var(--accent); text-transform: uppercase; letter-spacing: 0.5px;
  }
  .person-role { font-size: 18px; margin-top: 6px; }
  .divider {
    position: absolute; left: 322px; top: 170px;
    width: 2px; height: 66px; background: var(--accent);
  }
  .contacts {
    position: absolute; left: 344px; top: 166px;
    list-style: none; display: flex; flex-direction: column; gap: 6px;
    font-size: 18px;
  }
  .contacts li { display: flex; align-items: center; gap: 10px; }
  .contacts svg { width: 12px; height: 12px; flex: none; }
  .contacts .highlight { color: var(--accent); }
  .business-number {
    position: absolute; left: 150px; top: 300px; font-size: 19px;
  }
  .business-number .label { color: var(--accent); }
</style>
</head>
<body>
  <section class="card card--back" aria-label="Business card back">
    <div class="back-pattern" role="img" aria-label="Embossed repeating monogram pattern in dark grey"></div>
    <div class="back-brand"><span class="brand-square"></span>Holloway Paving Service</div>
  </section>

  <section class="card card--front" aria-label="Business card front">
    <div class="front-brand">
      <span class="brand-square"></span>
      <span class="brand-rule"></span>
      <div class="brand-text">
        <span class="brand-name">Holloway Paving Service</span>
        <span class="brand-phone">0418259730</span>
      </div>
    </div>

    <div class="person">
      <div class="person-name">Mark Holloway</div>
      <div class="person-role">Director</div>
    </div>
    <span class="divider"></span>

    <ul class="contacts">
      <li>
        <svg viewBox="0 0 12 12"><path d="M2.5 1 L4.5 1 L5.3 3.4 L4 4.4 C4.6 5.8 6.2 7.4 7.6 8 L8.6 6.7 L11 7.5 L11 9.5 C11 10.4 10.3 11 9.5 11 C5 11 1 7 1 2.5 C1 1.7 1.6 1 2.5 1 Z" fill="var(--accent)"/></svg>
        +61 418 259 730
      </li>
      <li>
        <svg viewBox="0 0 12 12"><rect x="0.8" y="2.3" width="10.4" height="7.4" fill="none" stroke="var(--accent)" stroke-width="1.2"/><path d="M1 2.6 L6 6.6 L11 2.6" fill="none" stroke="var(--accent)" stroke-width="1.2"/></svg>
        markholloway@brightmail.com.au
      </li>
      <li>
        <svg viewBox="0 0 12 12"><circle cx="6" cy="6" r="5" fill="none" stroke="var(--accent)" stroke-width="1.1"/><ellipse cx="6" cy="6" rx="2.2" ry="5" fill="none" stroke="var(--accent)" stroke-width="1"/><path d="M1 6 H11" stroke="var(--accent)" stroke-width="1"/></svg>
        <span>www.<span class="highlight">hollowaypaving</span>.com.au</span>
      </li>
    </ul>

    <p class="business-number"><span class="label">ABN :</span> 62318470915</p>
  </section>
</body>
</html>
```